Ridge Lass Crew (Flyer)

I want a flyer to advertise my service.
Details below, and logo's to use are attached.

A girls only after school program, 11-14yrs, as OSHC is no longer avail, dedicated to coaching & mentoring our girls into strong, independent young women.

The Brainchild of Rebecca Folwin, Ridge Lass Crew was created to address the growing demand for after school/school holiday supervision for kids moving from primary into high school, when OSHC ceases to exist.
With over 12 years experience mentoring and coaching young women in the corporate world, Bec decided to leave her role as a Director with Tarrant Trust, and follow her passion.
Bec, along with her sister Lorraine, who has over 10 years experience in local communities as a Youth Worker, and is also a qualified Enrolled Nurse, embarked on building a program designed to keep parents happy (by knowing their girls are safe) and dedicated to coaching and mentoring our girls into strong, independent young women.
Open every afternoon and during school holidays, we look to offer;
- Daily meditation
- Healthy snacks
- Dedicated homework time
- Organised group activity, led by qualified instructors (yoga, fitness class, soccer etc)
- Regular guests speakers, addressing issues/concerns for young people today
- SOCIAL MEDIA FREE ZONE

Located 87 Pelham Pde, Fernvale Heights (across from Crestmoor Day Clinic)
Open 3-6pm Monday to Friday

Facebook page: http://fb.example/ridgelasscrew
Email: info@ridgelasscrew.example.au
Mobile: 0455817396

Target Market(s)

Parents of teenage girls, teenage girls 11-14 years

Industry/Entity Type

School

Font styles to use
Sans Serif

Colors
b768aa
e667a6

Requirements
Must have
• What progam is - see brief
• Who runs it
Should not have
• Not be too busy, not overly mature images

```html
<!DOCTYPE html>
<html lang="en">
<head>
<meta charset="utf-8">
<title>Ridge Lass Crew – After School Program Flyer</title>
<link rel="stylesheet" href="https://fonts.googleapis.com/css2?family=Cinzel:wght@400;700&family=Roboto+Condensed:wght@400;700&family=Source+Sans+3:wght@400;600&family=Questrial&family=Pinyon+Script&display=swap">
<style>
  :root {
    --pink: #e667a6;
    --pink-deep: #d9559a;
    --mauve: #b768aa;
    --ink: #111111;
    --slate: #3b3c4c;
    --paper: #ffffff;
    --mist: #ececec;
  }
  html, body { margin: 0; padding: 0; overflow: hidden; }
  body { width: 848px; height: 1200px; background: var(--paper); }
  .flyer {
    position: relative; width: 848px; height: 1200px; overflow: hidden;
    background: linear-gradient(180deg, #ffffff 45%, var(--mist) 100%);
    font-family: "Source Sans 3", sans-serif; color: var(--ink);
  }
  .backdrop { position: absolute; inset: 0; }
  .photo-area { position: absolute; left: 0; top: 0; }
  .logo-panel {
    position: absolute; left: 606px; top: 4px; width: 220px; height: 294px;
    background: var(--paper); display: flex; align-items: center; justify-content: center;
    text-align: center;
  }
  .logo-name {
    font-family: "Source Sans 3", sans-serif; font-weight: 600; font-size: 34px;
    line-height: 1.1; color: var(--pink-deep);
  }
  .headline {
    position: absolute; right: 42px; top: 326px; margin: 0;
    font-family: "Cinzel", serif; font-weight: 700; font-size: 36px; color: var(--ink);
    letter-spacing: 1px;
  }
  .subhead {
    position: absolute; right: 6px; top: 386px; margin: 0;
    font-family: "Cinzel", serif; font-weight: 400; font-size: 27px; color: var(--ink);
    letter-spacing: 1.5px;
  }
  .age-range {
    position: absolute; left: 434px; top: 458px; margin: 0;
    font-family: "Cinzel", serif; font-weight: 700; font-size: 32px; color: var(--ink);
  }
  .age-note {
    position: absolute; right: 16px; top: 505px; margin: 0;
    font-family: "Questrial", sans-serif; font-size: 19px; color: var(--ink); letter-spacing: 0.5px;
  }
  .about-title {
    position: absolute; left: 64px; top: 598px; margin: 0;
    font-family: "Roboto Condensed", sans-serif; font-weight: 400; font-size: 29px; color: var(--ink);
  }
  .about-body {
    position: absolute; left: 27px; top: 662px; width: 400px; margin: 0;
    font-size: 21px; line-height: 29px; color: var(--ink);
  }
  .offer-title {
    position: absolute; left: 544px; top: 596px; margin: 0;
    font-family: "Questrial", sans-serif; font-weight: 700; font-size: 25px; color: var(--slate);
    letter-spacing: 0.5px;
  }
  .offer-list {
    list-style: none; margin: 0; padding: 0; position: absolute; left: 510px; top: 0;
    font-family: "Questrial", sans-serif; font-size: 20.5px; color: var(--ink);
  }
  .offer-list li { position: absolute; left: 0; white-space: nowrap; padding-left: 36px; }
  .offer-list li::before {
    content: ""; position: absolute; left: 4px; top: 8px; width: 8px; height: 8px;
    border-radius: 50%; background: var(--pink);
  }
  .offer-list .detail { display: block; padding-left: 9px; }
  .signoff {
    position: absolute; left: 0; width: 848px; text-align: center; margin: 0;
    font-family: "Cinzel", serif; color: var(--ink);
  }
  .signoff-lead { top: 940px; font-weight: 700; font-size: 24px; }
  .signoff-name { top: 978px; font-weight: 400; font-size: 38px; letter-spacing: 3px; }
  .tagline {
    position: absolute; left: 0; width: 848px; text-align: center; margin: 0;
    font-family: "Pinyon Script", cursive; font-size: 17px; color: var(--ink);
  }
  .tagline-1 { top: 1044px; }
  .tagline-2 { top: 1080px; }
  .contact-web {
    position: absolute; right: 592px; top: 1126px; margin: 0; text-align: right;
    font-size: 16px; line-height: 24px; color: var(--ink);
  }
  .contact-web .row { display: flex; justify-content: flex-end; align-items: center; gap: 6px; }
  .contact-web .label { font-size: 17px; }
  .contact-web .email, .contact-web .web { font-weight: 600; }
  .icon { width: 16px; height: 16px; flex: none; }
  .dot { width: 15px; height: 15px; border-radius: 50%; background: var(--ink); flex: none; }
  .contact-phone {
    position: absolute; left: 308px; top: 1152px; margin: 0;
    font-family: "Roboto Condensed", sans-serif; font-size: 22px; color: var(--ink); letter-spacing: 0.5px;
  }
  .contact-address {
    position: absolute; left: 576px; top: 1150px; margin: 0; display: flex; align-items: center; gap: 4px;
    font-family: "Roboto Condensed", sans-serif; font-weight: 700; font-size: 19px; color: var(--paper);
    letter-spacing: -0.3px; white-space: nowrap;
  }
</style>
</head>
<body>
<main class="flyer">
  <svg class="backdrop" width="848" height="1200" viewBox="0 0 848 1200" aria-hidden="true">
    <defs>
      <linearGradient id="footerBand" x1="0" y1="0" x2="1" y2="0">
        <stop offset="0" stop-color="#e667a6"/>
        <stop offset="0.55" stop-color="#d774ad"/>
        <stop offset="1" stop-color="#b768aa"/>
      </linearGradient>
      <linearGradient id="photoTones" x1="0" y1="0" x2="1" y2="1">
        <stop offset="0" stop-color="#c9372f"/>
        <stop offset="0.4" stop-color="#3f9b8f"/>
        <stop offset="0.75" stop-color="#5aa04a"/>
        <stop offset="1" stop-color="#e0b338"/>
      </linearGradient>
    </defs>
    <rect class="header-pink" x="0" y="0" width="848" height="438" fill="var(--pink)"/>
    <rect class="age-band" x="340" y="448" width="508" height="96" fill="var(--mauve)"/>
    <path class="footer-wave" d="M0 1108 C 250 1075, 560 1060, 848 1040 L848 1200 L0 1200 Z" fill="url(#footerBand)"/>
    <path class="footer-wave-tail" d="M500 1200 C 650 1150, 760 1120, 848 1100 L848 1200 Z" fill="var(--mauve)" opacity="0.7"/>
    <circle class="photo-ring" cx="180" cy="240" r="342" fill="var(--paper)"/>
  </svg>

  <svg class="photo-area" width="848" height="600" viewBox="0 0 848 600" role="img" aria-label="Photo of red canvas sneakers, spiral notebooks and pencils on a woven mat">
    <circle cx="180" cy="240" r="336" fill="url(#photoTones)"/>
  </svg>

  <div class="logo-panel">
    <span class="logo-name">Ridge<br>Lass<br>Crew</span>
  </div>

  <h1 class="headline">A Girls Only</h1>
  <h2 class="subhead">After School Program</h2>
  <p class="age-range">For 11-14yrs</p>
  <p class="age-note">as OSHC is no longer available</p>

  <h3 class="about-title">ABOUT US</h3>
  <p class="about-body">The Brainchild of Rebecca Folwin, Ridge Lass Crew was created to address the growing demand for after school/school holiday supervision for kids moving from primary into high school, when OSHC ceases to exist.</p>

  <h3 class="offer-title">WHAT WE OFFER</h3>
  <ul class="offer-list">
    <li style="top:645px">Daily meditation</li>
    <li style="top:685px">Healthy snacks</li>
    <li style="top:730px">Organised group activity,<span class="detail">(yoga, fitness class, soccer etc.)</span></li>
    <li style="top:783px">Regular guests speakers</li>
    <li style="top:833px">Dedicated homework time</li>
    <li style="top:879px">Social media free zone</li>
  </ul>

  <p class="signoff signoff-lead">The Brainchild of Rebecca Folwin</p>
  <p class="signoff signoff-name">Ridge Lass Crew</p>
  <p class="tagline tagline-1">Dedicated to Coaching &amp; Mentoring Our Girls</p>
  <p class="tagline tagline-2">into Strong, Independent Young women</p>

  <div class="contact-web">
    <div class="row"><span class="label">e-Mail us</span>
      <svg class="icon" viewBox="0 0 16 16" aria-hidden="true"><rect x="1.5" y="4" width="13" height="9" fill="none" stroke="#111" stroke-width="1.2"/><path d="M1.5 4 L8 9.5 L14.5 4" fill="none" stroke="#111" stroke-width="1.2"/></svg>
    </div>
    <div class="row email">info@ridgelasscrew.example.au</div>
    <div class="row web">http://fb.example/ridgelasscrew <span class="dot"></span></div>
  </div>

  <p class="contact-phone">CALL US: 0455817396</p>

  <p class="contact-address">
    <svg width="22" height="30" viewBox="0 0 22 30" aria-hidden="true"><path d="M11 1 C5 1 1 5.5 1 11 C1 18 11 29 11 29 C11 29 21 18 21 11 C21 5.5 17 1 11 1 Z" fill="#fff"/><circle cx="11" cy="11" r="4" fill="var(--mauve)"/></svg>
    87 Pelham Pde, Fernvale Heights
  </p>
</main>
</body>
</html>
```